Verdanith Website Concept

We would like a one page website. Please refer to the attached files for more information.

Please reference file attachment version 1.1.

```html
<!DOCTYPE html>
<html lang="en">
<head>
<meta charset="utf-8">
<title>Verdanith</title>
<link href="https://fonts.googleapis.com/css2?family=Open+Sans:wght@400;600;700&display=swap" rel="stylesheet">
<style>
:root{
  --bg:#4b5283;
  --navy:#3b4a84;
  --ink:#111;
  --muted:#8a8a8a;
  --gold:#f9c838;
  --line:#d8d8d8;
  --white:#fff;
}
*{box-sizing:border-box;margin:0;padding:0}
html,body{width:969px;height:1200px;overflow:hidden}
body{background:var(--bg);font-family:"Open Sans",sans-serif;position:relative}
.page{position:absolute;left:145px;top:36px;width:678px;height:1093px;background:var(--white);box-shadow:0 0 18px rgba(0,0,0,.35)}
.abs{position:absolute}
.brand{left:15px;top:14px;display:flex;align-items:center;gap:8px}
.brand-mark{width:34px;height:34px;border-radius:50%;background:var(--navy)}
.brand-name{font-size:20px;font-weight:400;color:var(--navy);letter-spacing:.5px}
.search{left:543px;top:16px;width:116px;height:34px;border:1px solid #ccc;border-radius:3px;display:flex;align-items:center;padding-left:12px;gap:7px;font-size:9.5px;color:#999}
.nav{left:0;top:65px;width:678px;height:39px;background:linear-gradient(#2a2a2a,#0d0d0d);display:flex}
.nav a{color:#fff;text-decoration:none;font-size:10.5px;display:flex;align-items:center;justify-content:center;border-right:1px solid #3a3a3a;height:100%}
.nav a.active{background:var(--gold);color:#222}
.hero{left:0;top:104px;width:678px;height:249px;background:linear-gradient(90deg,#4a4a4a 0%,#8a8580 35%,#d8c7b0 60%,#c9cdd4 80%,#e5e5e5 100%)}
.hero h1{position:absolute;left:18px;top:46px;width:200px;font-size:17.5px;font-weight:600;color:#fff;line-height:21px}
.hero p{position:absolute;left:18px;top:99px;width:206px;font-size:10px;line-height:11.6px;color:#e4e4e4}
.btn{background:#111;color:#fff;font-size:10px;border-radius:3px;display:flex;align-items:center;justify-content:center;box-shadow:0 1px 2px rgba(0,0,0,.4)}
.hero .btn{position:absolute;left:20px;top:163px;width:68px;height:24px;font-size:9px}
.dots{position:absolute;left:23px;top:206px;display:flex;gap:9px}
.dots span{width:8px;height:8px;border-radius:50%;border:1.5px solid #c8d0f0}
.dots span:first-child{background:#fff;border-color:#fff}
.heading{font-size:13px;font-weight:600;color:var(--navy);letter-spacing:.2px}
.svc{top:416px;width:149px}
.svc .ph{height:84px}
.svc h3{font-size:11.5px;font-weight:600;color:var(--ink);line-height:16.5px;margin-top:12px;height:40px}
.svc p{font-size:9.5px;line-height:16.8px;color:var(--muted)}
.rule{left:18px;width:641px;height:1px;background:var(--line)}
.welcome-img{left:18px;top:674px;width:196px;height:139px;background:linear-gradient(#7f8894,#3e444c)}
.welcome h2{position:absolute;left:230px;top:665px;font-size:17.5px;font-weight:400;color:var(--navy)}
.welcome p{position:absolute;left:230px;top:699px;width:210px;font-size:9px;line-height:16.8px;color:var(--muted)}
.consult{left:458px;top:640px;width:201px;height:238px;background:var(--gold);border-radius:3px}
.consult h3{position:absolute;left:14px;top:25px;font-size:12.5px;font-weight:600;color:var(--ink)}
.field{position:absolute;left:14px;width:152px;height:27px;background:#fff;font-size:10px;color:#555;padding:8px 9px}
.news .ph{width:128px;height:109px}
.news h3{font-size:13px;font-weight:400;color:var(--navy);white-space:nowrap}
.news p{font-size:9.5px;line-height:16.8px;color:#666;width:170px}
.footer{left:145px;top:1153px;font-size:9.5px;color:#fff;line-height:17px}
.social{top:1156px;width:25px;height:25px;border-radius:2px}
</style>
</head>
<body>
<div class="page">
  <div class="abs brand"><span class="brand-mark"></span><span class="brand-name">VERDANITH</span></div>
  <div class="abs search">
    <svg width="11" height="11" viewBox="0 0 11 11"><circle cx="4.5" cy="4.5" r="3.5" fill="none" stroke="#999" stroke-width="1.4"/><line x1="7" y1="7" x2="10.5" y2="10.5" stroke="#999" stroke-width="1.4"/></svg>SEARCH
  </div>
  <nav class="abs nav">
    <a class="active" style="width:68px">HOME</a>
    <a style="width:83px">ABOUT US</a>
    <a style="width:88px">SERVICES</a>
    <a style="width:104px">RECENT NEWS</a>
    <a style="width:97px;border:0">CONTACT US</a>
  </nav>
  <section class="abs hero" role="img" aria-label="Smiling woman resting her chin on a piggy bank">
    <h1>We are a financial security</h1>
    <p>Verdanith is a United States-based tier one security firm specializing in the protection of financial services professionals, executives and their families</p>
    <div class="btn">Read More</div>
    <div class="dots"><span></span><span></span><span></span></div>
  </section>

  <h2 class="abs heading" style="left:18px;top:391px">SERVICE OFFERINGS</h2>
  <div class="abs svc" style="left:18px">
    <div class="ph" role="img" aria-label="Hands framing a sunset landscape" style="background:linear-gradient(90deg,#5a3a2a,#c89a6a,#e8c8a0)"></div>
    <h3 style="margin-top:14px">Threat Assessment</h3>
    <p>Sed ut perspiciatis unde omnis iste natus error sit voluptatem accusan-tium doloremque laudantium,</p>
  </div>
  <div class="abs svc" style="left:182px">
    <div class="ph" role="img" aria-label="Elderly couple on a beach" style="background:linear-gradient(90deg,#d8d0c0,#c8b49a,#9a7a5a)"></div>
    <h3>Threat Avoidance Plan &amp; Dossier Creation</h3>
    <p>Sed ut perspiciatis unde omnis iste natus error sit voluptatem accusan-tium doloremque laudantium,</p>
  </div>
  <div class="abs svc" style="left:347px">
    <div class="ph" role="img" aria-label="Man with raised arms in a wheat field" style="background:linear-gradient(#5fb8c8,#a8c8b0 55%,#c89a40)"></div>
    <h3 style="margin-top:13px">Elite Executive Protection</h3>
    <p>Sed ut perspiciatis unde omnis iste natus error sit voluptatem accusan-tium doloremque laudantium,</p>
  </div>
  <div class="abs svc" style="left:509px">
    <div class="ph" role="img" aria-label="Businessman leaping over a city skyline" style="background:linear-gradient(#c8ccd2,#9aa0a8)"></div>
    <h3>Threat Avoidance Plan &amp; Dossier Maintenance</h3>
    <p>Sed ut perspiciatis unde omnis iste natus error sit voluptatem accusan-tium doloremque laudantium,</p>
  </div>

  <div class="abs rule" style="top:622px"></div>

  <div class="abs welcome-img" role="img" aria-label="Group of business people in suits"></div>
  <div class="welcome">
    <h2>Welcome to Verdanith</h2>
    <p>We deliver our services exclusively through associates and contractors with United States special operations, secret service, federal intelligence, or equivalent experience and training. We are one of only a handful of domestic security firms that offers scalable, tier one security services in every market in the United States.</p>
    <div class="abs btn" style="left:231px;top:837px;width:70px;height:25px">Read More</div>
  </div>

  <div class="abs consult">
    <h3>Request Consultation</h3>
    <div class="field" style="top:58px">Username</div>
    <div class="field" style="top:92px">Password</div>
    <div class="field" style="top:126px;width:167px;height:58px">Enter your Message</div>
    <div class="abs btn" style="left:13px;top:198px;width:43px;height:24px">Next</div>
  </div>

  <div class="abs rule" style="top:887px"></div>
  <h2 class="abs heading" style="left:19px;top:907px">LATEST NEWS</h2>

  <div class="news">
    <div class="abs ph" style="left:19px;top:944px;background:linear-gradient(#8a9aa0,#4a5258)" role="img" aria-label="Thoughtful young man with curly hair"></div>
    <h3 class="abs" style="left:162px;top:938px">Lorem ipsum dolor sit amet</h3>
    <p class="abs" style="left:164px;top:966px">Lorem ipsum dolor sit amet, consectetur adipisicing elit, sed do eiusmod tempor incididunt</p>
    <div class="abs btn" style="left:162px;top:1032px;width:70px;height:24px">Read More</div>

    <div class="abs ph" style="left:344px;top:944px;background:linear-gradient(90deg,#9ab8c8,#5a6a78)" role="img" aria-label="Businessman in a suit and tie"></div>
    <h3 class="abs" style="left:493px;top:938px">Lorem ipsum dolor sit amet</h3>
    <p class="abs" style="left:492px;top:966px">Lorem ipsum dolor sit amet, consectetur adipisicing elit, sed do eiusmod tempor incididunt</p>
    <div class="abs btn" style="left:490px;top:1032px;width:70px;height:24px">Read More</div>
  </div>
</div>

<div class="abs footer">
  <div>Home&nbsp; /&nbsp; About us&nbsp; /&nbsp; Services&nbsp; /&nbsp; Recent News&nbsp; /&nbsp; Contact us</div>
  <div style="font-size:8.5px">Copyright © 2014 . All rights reserved</div>
</div>
<div class="abs social" style="left:594px;background:#f5b21e"></div>
<div class="abs social" style="left:635px;background:#6cc6e8"></div>
<div class="abs social" style="left:675px;background:#3b5a9a"></div>
<div class="abs social" style="left:718px;background:#5fb0d0"></div>
<div class="abs social" style="left:759px;background:#d8282a"></div>
<div class="abs social" style="left:800px;background:#3a8ad8"></div>
</body>
</html>
```